Keto Food Brand Needs Packaging Design and Logo

We need a logo and packaging design for a stand-up food bag for our keto shake mix. We are a health and wellness brand launching our first shake mix product. I would like bold, bright colors. This document goes more in depth . This brand might encompass more than only food so I want the logo to be versatile for supplements and other health products. https://files.plavexa.net/doc/k7Rt2mQx9LpW4vZs8NcB3yHf6JdTa1Ue/view?share=link See images of logos attached. It doesn't have to be food for the logo but I like the creativity of the ones listed.

Target Market(s)

Keto. Health and Fitness

Logo Text

Zumora

Font styles to use
Serif
Sans Serif

Colors

Designer to choose colors to be used in the design.

```html
<!DOCTYPE html>
<html lang="en">
<head>
<meta charset="utf-8">
<title>Zumora Keto Shake Mix – Pouch Proof</title>
<link href="https://fonts.googleapis.com/css2?family=Alfa+Slab+One&family=Lato:ital,wght@0,400;0,700;0,900;1,900&family=Montserrat:wght@800&family=Open+Sans:wght@400;700&family=Rye&display=swap" rel="stylesheet">
<style>
:root{
  --orange:#e8901f;
  --orange-deep:#d9761a;
  --orange-box:#f08a1c;
  --white:#ffffff;
  --ink:#222222;
  --dim:#666666;
  --dieline:#e060b0;
  --cut:#d42a1c;
  --notch:#1aa3e8;
  --seal:#dcecf6;
  --red:#e0201a;
}
*{box-sizing:border-box;margin:0;padding:0}
html,body{width:1200px;height:638px;overflow:hidden;background:var(--white)}
body{position:relative;font-family:"Open Sans",Arial,sans-serif;color:var(--ink)}
.abs{position:absolute}
.dim{font-size:7px;color:var(--dim);white-space:nowrap}
.guides{position:absolute;left:0;top:0}

/* panels */
.panel-back{left:124px;top:58px;width:400px;height:382px;background:linear-gradient(135deg,#eb9726,#e0841a 60%,#e99325)}
.panel-front{left:676px;top:58px;width:396px;height:382px;background:linear-gradient(160deg,#ea9424,#dc7d18)}
.seal-band{left:64px;top:432px;width:1072px;height:8px;background:var(--seal)}

.back-copy{left:144px;top:90px;width:182px;height:252px;overflow:hidden;color:var(--white);font-family:"Lato",sans-serif;font-weight:700;font-size:6.5px;line-height:10.1px;text-align:center;hyphens:auto}
.back-wide{left:146px;top:348px;width:346px;height:42px;overflow:hidden;color:var(--white);font-family:"Lato",sans-serif;font-weight:700;font-size:6.5px;line-height:10.1px}
.label-window{left:336px;top:90px;width:156px;height:248px;background:var(--white)}

/* gusset */
.gusset-mark{left:574px;top:146px;width:38px;height:38px;border-radius:50%;background:var(--orange)}
.gusset-name{left:600px;top:290px;transform:translate(-50%,-50%) rotate(90deg);font-family:"Montserrat",sans-serif;font-weight:800;font-size:40px;color:var(--orange);white-space:nowrap}

/* front */
.front-wave{left:676px;top:58px}
.brand{left:790px;top:78px;display:flex;align-items:center;gap:8px}
.brand-dot{width:30px;height:30px;border-radius:50%;background:var(--orange)}
.brand-name{font-family:"Montserrat",sans-serif;font-weight:800;font-size:28px;color:var(--orange);letter-spacing:.5px}
.keto{left:732px;top:140px;font-family:"Rye",serif;font-size:70px;line-height:1;color:var(--white);letter-spacing:4px}
.flavour{left:730px;top:252px;font-family:"Alfa Slab One",serif;font-size:23px;color:var(--white)}
.subtitle{left:731px;top:280px;font-family:"Lato",sans-serif;font-weight:900;font-style:italic;font-size:16px;color:var(--white)}
.claims{left:722px;top:324px;width:98px;height:100px;border-radius:10px;background:var(--orange-box);overflow:hidden;text-align:center;color:var(--white);font-family:"Lato",sans-serif;font-size:6px}
.claims li{list-style:none;padding:4px 4px;border-bottom:1px solid rgba(255,255,255,.8);margin:0 8px}
.claims li:first-child{line-height:7px}
.claims-foot{position:absolute;left:0;bottom:0;width:100%;height:22px;background:var(--white);color:var(--orange);padding-top:3px;font-size:5.5px;line-height:7px}
.claims-foot b{font-weight:900;font-size:6px}
.product-photo{left:908px;top:292px;width:164px;height:136px;background:linear-gradient(170deg,#f6f1dc 0%,#efe6c4 60%,#c99a5a 82%,#b07a3a 100%);border-radius:60% 0 6px 6px/30% 0 6px 6px}

/* info block */
.info{font-size:7px;color:var(--ink);white-space:nowrap;line-height:9px}
.swatch{display:inline-block;width:9px;height:9px;border:1px solid #000;margin-right:5px;vertical-align:-2px}
.note{left:170px;top:570px;width:378px;height:58px;border:1px solid #000;padding:3px 4px;font-size:5.1px;line-height:7.1px;overflow:hidden}
.note b{color:var(--red)}
.checklist{left:702px;top:548px;width:160px;height:76px;border:1.2px solid #000;padding:3px 6px;font-size:6.4px;line-height:10px}
.checklist .t{color:var(--red);font-weight:700}
.checklist div{text-align:right}
.checklist span{color:var(--red)}
.box{display:inline-block;width:6px;height:6px;border:1px solid #000;margin-left:4px;vertical-align:-1px}
.approval{left:872px;top:570px;width:158px;height:54px;border:1.2px solid #000;padding:3px 6px;font-size:3.8px;line-height:5px;white-space:nowrap;overflow:hidden}
.approval .row{margin-top:6px;padding-left:14px}
.approval .box{width:5px;height:5px;margin:0 4px 0 2px}
.rev{left:894px;top:552px;font-family:"Lato",sans-serif;font-weight:900;font-size:10px}
.tol{color:var(--red)}
</style>
</head>
<body>

<div class="abs panel-back"></div>
<div class="abs panel-front"></div>

<svg class="abs front-wave" width="396" height="140" viewBox="0 0 396 140" aria-hidden="true">
  <path d="M0 0H396V0 L396 0 C370 20 350 60 340 40 C320 10 290 50 250 62 C210 74 190 40 140 48 C90 56 60 100 30 90 C15 86 5 70 0 60Z" fill="#ffffff"/>
</svg>

<div class="abs seal-band"></div>

<svg class="guides" width="1200" height="638" viewBox="0 0 1200 638" aria-hidden="true">
  <g stroke="#999" stroke-width=".6" fill="none">
    <path d="M42 12H1158M42 8V20M1158 8V20"/>
    <path d="M64 38H524M524 38H676M676 38H1136M64 30V46M524 30V46M676 30V46M1136 30V46"/>
    <path d="M52 58V440M48 58H56M48 440H56"/>
    <path d="M64 452V466H120M120 452V470M64 474H120"/>
    <path d="M446 466H524M524 452V466M460 478H538"/>
    <path d="M42 480H1158M42 474V486M1158 474V486"/>
    <path d="M170 490H1030"/>
  </g>
  <rect x="64" y="58" width="1072" height="382" fill="none" stroke="var(--dieline)" stroke-width=".8"/>
  <rect x="64" y="58" width="60" height="382" fill="none" stroke="#d0e6f3" stroke-width=".6"/>
  <rect x="1072" y="58" width="64" height="382" fill="none" stroke="#d0e6f3" stroke-width=".6"/>
  <g stroke="var(--cut)" stroke-width=".8" fill="none">
    <path d="M124 58V440M128 58V440M524 58V440M676 58V440M1072 58V440M1068 58V440"/>
    <path d="M116 58V440M1080 58V440" stroke="#3a3a8a"/>
  </g>
  <g stroke="var(--dieline)" stroke-width=".8" stroke-dasharray="4 3" fill="none">
    <path d="M68 64H1132M68 434H1132M70 64V434M1130 64V434"/>
    <path d="M130 64V434M520 64V434M530 64V434M672 64V434M680 64V434"/>
  </g>
  <g stroke="var(--notch)" stroke-width="1.2" fill="var(--notch)">
    <path d="M98 58V440M1102 58V440"/>
    <path d="M93 52L103 52L98 58Z M93 446L103 446L98 440Z M1097 52L1107 52L1102 58Z M1097 446L1107 446L1102 440Z"/>
  </g>
  <rect x="40" y="432" width="18" height="9" fill="#000"/>
  <rect x="1140" y="432" width="18" height="9" fill="#000"/>
  <g stroke-width="1">
    <path d="M640 586H658" stroke="var(--dieline)"/>
    <path d="M640 600H658" stroke="var(--notch)"/>
    <circle cx="640" cy="600" r="1.5" fill="var(--notch)"/>
    <path d="M640 610H658" stroke="var(--dieline)" stroke-dasharray="3 3"/>
    <path d="M640 618H658" stroke="var(--dieline)" stroke-dasharray="4 2"/>
  </g>
</svg>

<span class="abs dim" style="left:566px;top:3px">28.0000 in &nbsp; 711.2 mm</span>
<span class="abs dim" style="left:244px;top:30px">12.000 in &nbsp; 304.8 mm</span>
<span class="abs dim" style="left:568px;top:30px">4.0000 in &nbsp; 101.6 mm</span>
<span class="abs dim" style="left:880px;top:30px">12.000 in &nbsp; 304.8 mm</span>
<span class="abs dim" style="left:26px;top:242px;line-height:9px">10.0000 in<br>254 mm</span>
<span class="abs dim" style="left:1138px;top:58px;line-height:9px">0.2500 in<br>6.35mm</span>
<span class="abs dim" style="left:65px;top:451px;line-height:9px">0.8750 in<br>22.225 mm</span>
<span class="abs dim" style="left:64px;top:470px">1.5000 in &nbsp; 38.1 mm</span>
<span class="abs dim" style="left:493px;top:451px;line-height:9px">0.1250 in<br>3.175 mm</span>
<span class="abs dim" style="left:461px;top:471px">2.0000 in 50.8 mm</span>
<span class="abs dim" style="left:560px;top:482px">29.25 in 742.95 mm</span>

<div class="abs back-copy">
  <p>Lorem ipsum dolor sit amet, consectetuer adipiscing elit, sed diam nonummy nibh euismod tincidunt ut laoreet dolore magna aliquam erat volutpat. Ut wisi enim ad minim veniam, quis nostrud exerci tation ullamcorper suscipit lobortis nisl ut aliquip ex ea commodo consequat. Duis autem vel eum iriure dolor in hendrerit in vulputate velit esse molestie consequat, vel illum dolore eu feugiat nulla facilisis at vero eros et accumsan et iusto odio dignissim qui blandit praesent luptatum zzril delenit augue duis dolore te feugait nulla facilisi.</p>
  <p>Lorem ipsum dolor sit amet, cons ectetuer adipiscing elit, sed diam nonummy nibh euismod tincidunt ut laoreet dolore magna aliquam erat volutpat. Ut wisi enim ad minim veniam, quis nostrud exerci tation ullamcorper suscipit lobortis nisl ut aliquip ex ea commodo consequat.</p>
  <p>Lorem ipsum dolor sit amet, consectetuer adipiscing elit, sed diam nonummy nibh euismod tincidunt ut laoreet dolore magna aliquam erat volutpat. Ut wisi enim ad minim veniam, quis nostrud exerci tation ullamcorper suscipit lobortis nisl ut aliquip ex ea commodo consequat. Duis autem vel eum iriure dolor in hendrerit in vulputate velit esse molestie consequat, vel illum dolore eu feugiat nulla facilisis at vero eros et accumsan et iusto odio dignissim qui blandit praesent luptatum zzril delenit augue duis dolore te feugait nulla facilisi.</p>
</div>
<div class="abs label-window"></div>
<p class="abs back-wide">Lorem ipsum dolor sit amet, consectetuer adipiscing elit, sed diam nonummy nibh euismod tincidunt ut laoreet dolore magna aliquam erat volutpat. Ut wisi enim ad minim veniam, quis nostrud exerci tation ullamcorper suscipit lobortis nisl ut aliquip ex ea commodo consequat. Duis autem vel eum iriure dolor in hendrerit in vulputate velit esse molestie consequat, vel illum dolore eu feugiat nulla facilisis at vero eros et accumsan et iusto odio dignissim qui blandit praesent luptatum zzril delenit augue duis dolore te</p>

<div class="abs gusset-mark"></div>
<div class="abs gusset-name">Zumora</div>

<div class="abs brand"><span class="brand-dot"></span><span class="brand-name">Zumora</span></div>
<div class="abs keto">KETO</div>
<div class="abs flavour">CHEESECAKE</div>
<div class="abs subtitle">Keto Shake Mix.</div>
<ul class="abs claims">
  <li>NEW YOUR STYLE AND<br>CHEESSY AND CHOKLATE</li>
  <li>KETO FRINEDLY</li>
  <li>LOW CARB</li>
  <li>NO ADDED SUGAR</li>
  <li class="claims-foot" style="margin:0;border:0"><b>DIETARY SUPPLEMENT</b><br>Net Wt 1.04lb (470 grams)</li>
</ul>
<div class="abs product-photo" role="img" aria-label="Photo of a slice of cheesecake with a biscuit crust"></div>

<div class="abs info" style="left:170px;top:498px">Date: 10.15.19</div>
<div class="abs info" style="left:170px;top:522px">Project Name:</div>
<div class="abs info" style="left:170px;top:538px">Sku name</div>
<div class="abs info" style="left:170px;top:558px">Template Name: 10.000 W x 12.00 H + 4.000 G</div>
<div class="abs info" style="left:302px;top:498px">Material:<br>Material</div>
<div class="abs info" style="left:410px;top:498px">Features:</div>
<div class="abs info" style="left:410px;top:516px">Tear: .875"</div>
<div class="abs info" style="left:410px;top:532px">Zipper: 1.5"</div>
<div class="abs info" style="left:410px;top:548px">Hanghole: No</div>
<div class="abs info" style="left:488px;top:498px">Measurements:</div>
<div class="abs info" style="left:488px;top:516px">Bleed: 0.125"<br>Each Side</div>
<div class="abs info" style="left:488px;top:544px">Eyemarks<br>&nbsp;0.5" x 0.25"</div>
<div class="abs info" style="left:568px;top:498px">Color Specifications:</div>
<div class="abs info" style="left:568px;top:508px;line-height:12px">
  <span class="swatch" style="background:#fff"></span>White<br>
  <span class="swatch" style="background:#1aa3e8"></span>Cyan<br>
  <span class="swatch" style="background:#e0147a"></span>Magenta<br>
  <span class="swatch" style="background:#ffe600"></span>Yellow<br>
  <span class="swatch" style="background:#000"></span>Black
</div>
<div class="abs info" style="left:704px;top:498px">Color Strategy:</div>
<div class="abs info" style="left:878px;top:498px">LUTs:<br>XP05</div>
<div class="abs info" style="left:942px;top:498px">Tolerances:<br><span class="tol">All Measurements are<br>+/- 2mm/0.078in</span></div>
<div class="abs info tol" style="left:942px;top:524px">Please note: Seal sizes and<br>location are approximate</div>

<div class="abs info" style="left:638px;top:572px;line-height:8px">Legend:<br><span style="padding-left:22px">Dieline</span><br><span style="padding-left:22px">Seal</span><br><span style="padding-left:22px">Tear Notch</span><br><span style="padding-left:22px">Zipper</span><br><span style="padding-left:22px">Safe Area</span></div>

<div class="abs note"><b>PLEASE CHECK CAREFULLY:</b> Proofs are supplied for proofing of layout, spelling, sizing, features and color breaks.<br>Please indicate any corrections needed at once. If no changes are necessary, please sign and return.<br>Production will not start until proof is approved and returned. Your approval is our authority to proceed.<br>Delay in returning your proof will delay your delivery. We have checked this artwork for accuracy. Final approval is the client's responsibility.<br>Please check for errors before production. Customer assumes all risk for compliance with federal, state and local packaging, advertising and<br>labeling laws, regulations and rules. This proof is for layout and copy only and does not reflect final color achievable on press.</div>

<div class="abs checklist">
  <p class="t">CUSTOMER PROOF APPROVAL CHECKLIST:</p>
  <div><span>SIZE LISTED</span> IS CORRECT:<i class="box"></i></div>
  <div><span>POUCH FEATURES</span> ARE CORRECT:<i class="box"></i></div>
  <div><span>SEALS</span> ARE CORRECT:<i class="box"></i></div>
  <div><span>UPC</span> IS CORRECT:<i class="box"></i></div>
  <div><span>SPELLING</span> IS CORRECT:<i class="box"></i></div>
  <div><span>COLORS</span> ARE CORRECT:<i class="box"></i></div>
</div>

<div class="abs rev">Rev: 0 Created by: RR</div>
<div class="abs approval">
  <p style="text-align:center">YOUR SIGNED APPROVAL IS REQUIRED FOR US TO PROCEED. BY SIGNING,<br>YOU ASSUME RESPONSIBILITY FOR THE ACCURACY OF THIS PROOF.</p>
  <p class="row">APPROVED AS IS<i class="box"></i>SIGNATURE:____________________________</p>
  <p class="row">APPROVED WITH CHANGES<i class="box"></i>SIGNATURE:______________________</p>
  <p class="row">NOT APPROVED<i class="box"></i>SIGNATURE:_____________________________</p>
</div>

</body>
</html>
```